Commercial Loan Originator Business Card (CHANGE COLORS SCHEME)

CHANGE COLOR SCHEME - SAME DESIGN

Name Marlene Agate
Title Commercial Loan Originator
Office (800) 417-2906 x68
Direct (240) 615-2043
Email freshgreens4life@quillbox.example

Name Dale Morrow
Office (800) 417-2906 x70
Direct (410) 392-5184
Email d.morthehomeguy@quillbox.example

Name Leonard Vasko
Office (800) 417-2906 x71
Direct (215) 463-0712
Email l.vasko41@quillbox.example

Name Gwen Halsey
Office (800) 417-2906 x
Direct (202) 548-1370
Email ghalsey63@quillbox.example

Name Mirna Ashby
Office (800) 417-2906 x72
Direct (240) 871-4526
Email tristatehomelending@quillbox.example

```html
<!DOCTYPE html>
<html lang="en">
<head>
<meta charset="UTF-8">
<title>Leonard Vasko – Business Card</title>
<link rel="stylesheet" href="https://fonts.googleapis.com/css2?family=Montserrat:wght@400;500;700&display=swap">
<style>
  :root {
    --backdrop: #c9c9cc;
    --card: #ffffff;
    --accent: #0e5e57;
    --accent-soft: #c79a3b;
    --ink: #2b2f2e;
    --photo-light: #7d94b3;
    --photo-dark: #1c2a4a;
  }
  * { box-sizing: border-box; margin: 0; padding: 0; }
  html, body {
    width: 1200px; height: 788px; overflow: hidden;
    background: var(--backdrop);
    font-family: "Montserrat", sans-serif;
  }
  .business-card {
    position: absolute; left: 75px; top: 94px;
    width: 1050px; height: 600px;
    background: var(--card);
    border-radius: 32px;
    box-shadow: 0 10px 30px rgba(0,0,0,.18);
  }
  .identity { position: absolute; left: 66px; top: 168px; }
  .identity__name {
    font-weight: 700; font-size: 44px; letter-spacing: .5px;
    color: var(--accent); text-transform: uppercase; line-height: 1;
  }
  .identity__title {
    margin-top: 8px; font-size: 23px; font-weight: 400;
    color: var(--ink); letter-spacing: .6px;
  }
  .divider {
    position: absolute; left: 66px; top: 276px;
    width: 600px; height: 2px; background: var(--accent-soft);
  }
  .portrait {
    position: absolute; left: 652px; top: 120px;
    width: 336px; height: 336px; border-radius: 50%;
    border: 6px solid var(--accent);
    background: radial-gradient(circle at 55% 45%, var(--photo-light) 0%, #4d6589 45%, var(--photo-dark) 100%);
  }
  .contacts { position: absolute; left: 70px; top: 292px; list-style: none; }
  .contacts__item {
    display: flex; align-items: center; gap: 14px;
    height: 48px; font-size: 29px; color: var(--ink); letter-spacing: .5px;
  }
  .contacts__icon { width: 24px; height: 24px; flex: none; fill: var(--accent); }
</style>
</head>
<body>
  <div class="business-card">
    <div class="identity">
      <div class="identity__name">Leonard Vasko</div>
      <div class="identity__title">Commercial Loan Originator</div>
    </div>
    <div class="divider"></div>
    <div class="portrait" role="img" aria-label="Portrait photo of Leonard Vasko in a navy suit, city office window behind"></div>
    <ul class="contacts">
      <li class="contacts__item">
        <svg class="contacts__icon" viewBox="0 0 24 24" aria-hidden="true"><path d="M6.6 10.8a15.1 15.1 0 0 0 6.6 6.6l2.2-2.2a1 1 0 0 1 1-.25 11.4 11.4 0 0 0 3.6.57 1 1 0 0 1 1 1V20a1 1 0 0 1-1 1A17 17 0 0 1 3 4a1 1 0 0 1 1-1h3.5a1 1 0 0 1 1 1c0 1.25.2 2.45.57 3.57a1 1 0 0 1-.25 1z"/></svg>
        <span>(800) 417-2906 x71</span>
      </li>
      <li class="contacts__item">
        <svg class="contacts__icon" viewBox="0 0 24 24" aria-hidden="true"><path d="M7 1h10a2 2 0 0 1 2 2v18a2 2 0 0 1-2 2H7a2 2 0 0 1-2-2V3a2 2 0 0 1 2-2zm0 3v14h10V4zm5 15.2a1.2 1.2 0 1 0 0 2.4 1.2 1.2 0 0 0 0-2.4z"/></svg>
        <span>(215) 463-0712</span>
      </li>
      <li class="contacts__item">
        <svg class="contacts__icon" viewBox="0 0 24 24" aria-hidden="true"><path d="M2 5h20v14H2zm2 2v.4l8 5.2 8-5.2V7zm0 2.8V17h16V9.8l-8 5.2z"/></svg>
        <span>l.vasko41@quillbox.example</span>
      </li>
    </ul>
  </div>
</body>
</html>
```